Exciting new vermouth brand needs a brilliant label!

We need a label design for an exciting new premium Italian Vermouth brand called Brunallo Vermouth.

Brunallo Vermouth is based on a recipe that has been handed down for four generations and is made in the traditional way in the Piedmonte region of Northern Italy.

Brunallo, which means 'heavenly' in Italian has been designed to elevate classic cocktails such as the Negroni, Americano and Manhattan with a base of Italian wine blended with botanicals such as wormwood, orange peel, rhubarb and cinchona. It has a delicately balanced bittersweet profile with hints of vanilla and citrus.

Its competitors include brands such as Doralte Mirena, Bellusi and Grevano (see the uploaded brief for more examples).

The label is for a 50cl dark bottle (please refer to the uploaded brief) and should be based on maximum dimensions of 70mm (width) x 110mm (height). There is no limit to embellishments such as foil printing, embossing or any other premium finishes. The label does not necessarily need to be rectangular.

Feedback will be given quickly and constructively after submissions to ensure that the process is as fair and useful as possible for everyone.

Target Market(s)

25-45 year old Europeans, 50:50 female:male

Industry/Entity Type

Wine / Spirits / Vermouth

Requirements
Must have
• Fantastic design that is distinct from competitors, a premium feel and great lettering.
Should not have
• Generic images or patterns that do not relate to the brand (Brunallo) or the product

```html
<!DOCTYPE html>
<html lang="en">
<head>
<meta charset="utf-8">
<title>Brunallo Vermouth – Label</title>
<link rel="stylesheet" href="https://fonts.googleapis.com/css2?family=Playfair+Display:wght@700&family=Italiana&family=Montserrat:wght@400;600&display=swap">
<style>
  :root {
    --gold-light: #e6d394;
    --gold: #c8ad63;
    --gold-deep: #a2843a;
    --label-black: #060504;
    --page: #ffffff;
  }
  html, body {
    margin: 0;
    padding: 0;
    width: 1200px;
    height: 1200px;
    overflow: hidden;
    background: var(--page);
  }
  .canvas {
    position: relative;
    width: 1200px;
    height: 1200px;
  }
  .label {
    position: absolute;
    left: 322px;
    top: 152px;
    width: 557px;
    height: 888px;
  }
  .brand-name {
    font-family: "Playfair Display", "Didot", serif;
    font-weight: 700;
    font-size: 78px;
    fill: var(--gold);
  }
  .product-type {
    font-family: "Italiana", "Didot", serif;
    font-size: 60px;
    fill: var(--gold);
  }
  .origin {
    font-family: "Montserrat", "Helvetica Neue", sans-serif;
    font-weight: 600;
    font-size: 18px;
    letter-spacing: 4px;
    fill: var(--gold);
  }
  .description, .volume {
    font-family: "Montserrat", "Helvetica Neue", sans-serif;
    font-weight: 400;
    fill: var(--gold);
  }
  .description { font-size: 14.5px; }
  .volume { font-size: 12px; }
  .frame-line {
    fill: none;
    stroke: var(--gold);
    stroke-width: 3;
  }
</style>
</head>
<body>
<div class="canvas">
  <svg class="label" viewBox="0 0 557 888" xmlns="http://www.w3.org/2000/svg">
    <defs>
      <linearGradient id="foil" x1="0" y1="0" x2="1" y2="1">
        <stop offset="0" stop-color="var(--gold-deep)"/>
        <stop offset="0.45" stop-color="var(--gold-light)"/>
        <stop offset="1" stop-color="var(--gold-deep)"/>
      </linearGradient>
      <radialGradient id="emblemGlow" cx="0.5" cy="0.5" r="0.5">
        <stop offset="0" stop-color="var(--gold)" stop-opacity="0.55"/>
        <stop offset="1" stop-color="var(--gold)" stop-opacity="0.08"/>
      </radialGradient>
      <path id="brandArc" d="M88 232 Q278 196 468 232"/>
    </defs>

    <!-- foil border and black field -->
    <path class="label-foil" fill="url(#foil)"
          d="M0 888 L14 200 C14 60 140 0 278 0 C416 0 543 60 543 200 L557 888 Z"/>
    <path class="label-field" fill="var(--label-black)"
          d="M17 869 L30 200 C30 80 150 18 278 18 C406 18 527 80 527 200 L538 869 Z"/>

    <!-- fine gold frame -->
    <line class="frame-line" x1="182" y1="66" x2="376" y2="66"/>
    <path class="frame-line" d="M42 858 L42 230 C42 120 140 82 278 82 C416 82 514 120 514 230 L514 858 Z"/>
    <line class="frame-line" x1="68" y1="285" x2="68" y2="490"/>
    <line class="frame-line" x1="489" y1="285" x2="489" y2="490"/>
    <line class="frame-line" x1="42" y1="533" x2="514" y2="533"/>
    <line class="frame-line" x1="42" y1="648" x2="514" y2="648"/>

    <!-- brand name -->
    <text class="brand-name" text-anchor="middle">
      <textPath href="#brandArc" startOffset="50%" textLength="380" lengthAdjust="spacingAndGlyphs">BRUNALLO</textPath>
    </text>

    <!-- emblem area -->
    <ellipse class="emblem" cx="278" cy="390" rx="170" ry="130" fill="url(#emblemGlow)"
             role="img" aria-label="Gold line illustration of a phoenix with outstretched wings beneath small stars"/>

    <!-- product type box -->
    <rect class="frame-line" x="74" y="553" width="390" height="72"/>
    <text class="product-type" x="269" y="611" text-anchor="middle">VERMOUTH</text>

    <!-- description box -->
    <rect class="frame-line" x="82" y="698" width="374" height="124"/>
    <text class="origin" x="269" y="742" text-anchor="middle">PREMIUM ITALIAN</text>
    <text class="description" x="269" y="775" text-anchor="middle">WINE BLENDED</text>
    <text class="description" x="269" y="794" text-anchor="middle">WITH BOTANICALS</text>
    <rect x="232" y="812" width="74" height="16" fill="var(--label-black)"/>
    <text class="volume" x="269" y="826" text-anchor="middle">500ML</text>
  </svg>
</div>
</body>
</html>
```